Business Card Design For Marketing Agnecy LVP

Need business card design for marketing agency.

Doug Fenwick
President, CEO
1-555-302-4196
doug@boldpromoperksgroup.example
www.BoldPromoPerksGroup.example

Back Side:
Boost Sales Using Rewards, Incentives & Giveaways
Get A Free Sample Package

Target Market(s)

B2B

Industry/Entity Type

Marketing

Contact Information for Business Card

Doug Fenwick
President, CEO
1-555-302-4196

Back Side:
Get A Free Sample Package

Please note that my current url is OLD DESIGN. I am working on new design and want the business card to match color themes at least on new site. Here is the demo link for new site so you can see the colors I use, etc.

http://layoutcratehub.example/kq/doug/lvp_final/index.html

Requirements
Must have
• Please note that my current url is OLD DESIGN. I am working on new design and want the business card to match color themes at least on new site. Here is the demo link for new site so you can see the colors I use, etc.

Nice to have

Should not have

```html
<!DOCTYPE html>
<html lang="en">
<head>
<meta charset="utf-8">
<title>LVP Business Card</title>
<link rel="stylesheet" href="https://fonts.googleapis.com/css2?family=Arimo:wght@400;700&family=Montserrat:wght@600;700&display=swap">
<style>
  :root {
    --bg: #0a0a0b;
    --card: #2a2a2c;
    --card-edge: #1f1f21;
    --blue: #1f7fd3;
    --blue-deep: #1766b0;
    --grey-text: #c9c9cb;
    --muted: #8a8a8d;
    --rule: #4a4a4d;
    --mark-grey: #7d7d80;
  }
  * { margin: 0; padding: 0; box-sizing: border-box; }
  html, body { width: 1200px; height: 822px; overflow: hidden; background: var(--bg); }
  .stage {
    position: relative; width: 1200px; height: 822px;
    display: flex; justify-content: center; align-items: center; gap: 60px;
  }
  .card {
    position: relative; width: 500px; height: 286px;
    background: var(--card);
    border-radius: 3px;
    box-shadow: 0 18px 40px rgba(0,0,0,.6);
    font-family: "Arimo", Arial, sans-serif;
  }
  .card--front { border-bottom: 3px solid var(--blue); border-left: 2px solid var(--blue); }
  .card--back {
    border-bottom: 3px solid var(--blue);
    box-shadow: 0 3px 0 var(--card-edge), 0 6px 0 var(--blue-deep), 0 9px 0 var(--card-edge), 0 12px 0 var(--blue-deep), 0 26px 40px rgba(0,0,0,.6);
  }

  /* front */
  .brand-name {
    position: absolute; right: 40px; top: 34px;
    font-family: "Montserrat", Arial, sans-serif; font-weight: 700;
    font-size: 68px; letter-spacing: 2px; color: var(--blue); line-height: 1;
  }
  .brand-rule { position: absolute; right: 30px; top: 126px; width: 260px; height: 1px; background: var(--rule); }
  .person { position: absolute; left: 34px; top: 158px; }
  .person__name {
    font-family: "Montserrat", Arial, sans-serif; font-weight: 700;
    font-size: 17px; color: var(--blue); letter-spacing: .5px;
  }
  .person__role { font-size: 14px; color: var(--grey-text); margin-top: 2px; }
  .person-rule { position: absolute; left: 200px; top: 170px; width: 268px; height: 1px; background: var(--rule); }
  .contacts { position: absolute; left: 36px; top: 208px; list-style: none; }
  .contacts li {
    display: flex; align-items: center; gap: 8px;
    font-size: 13.5px; color: var(--grey-text); line-height: 19px;
  }
  .contacts svg { width: 11px; height: 11px; fill: var(--blue); flex: none; }

  /* back */
  .back-mark {
    position: absolute; left: 0; right: 0; top: 52px; text-align: center;
    font-family: "Montserrat", Arial, sans-serif; font-weight: 700;
    font-size: 84px; letter-spacing: 3px; color: var(--mark-grey); line-height: 1;
  }
  .tagline {
    position: absolute; left: 0; right: 0; top: 164px; text-align: center;
    font-size: 14px; color: #e4e4e6; line-height: 18px;
  }
  .tagline .dot { display: inline-block; width: 6px; height: 6px; border-radius: 50%; background: #e4e4e6; margin: 0 6px; vertical-align: middle; }
  .back-rule { position: absolute; left: 140px; right: 140px; top: 212px; height: 1px; background: var(--rule); }
  .back-url { position: absolute; left: 0; right: 0; top: 222px; text-align: center; font-size: 13px; color: var(--grey-text); }
</style>
</head>
<body>
<main class="stage">
  <section class="card card--front" aria-label="Business card front">
    <div class="brand-name">LVP</div>
    <div class="brand-rule"></div>
    <div class="person">
      <div class="person__name">DOUG FENWICK</div>
      <div class="person__role">President, CEO</div>
    </div>
    <div class="person-rule"></div>
    <ul class="contacts">
      <li><svg viewBox="0 0 12 12"><path d="M2.5 1l2 2.2-1 1.3c.7 1.4 1.7 2.4 3 3l1.3-1L10 8.5 8.8 11C4.5 10.6 1.4 7.5 1 3.2z"/></svg>1-555-302-4196</li>
      <li><svg viewBox="0 0 12 12"><path d="M1 2.5h10v7H1z M1.6 3l4.4 3.4L10.4 3" stroke="#2a2a2c" stroke-width=".9"/></svg>doug@boldpromoperksgroup.example</li>
      <li><svg viewBox="0 0 12 12"><circle cx="6" cy="6" r="5"/><path d="M1 6h10M6 1c-2 2.6-2 7.4 0 10M6 1c2 2.6 2 7.4 0 10" stroke="#2a2a2c" stroke-width=".8" fill="none"/></svg>www.BoldPromoPerksGroup.example</li>
    </ul>
  </section>

  <section class="card card--back" aria-label="Business card back">
    <div class="back-mark">LVP</div>
    <p class="tagline">Boost Sales Using Rewards<span class="dot"></span>Incentives &amp; Giveaways<br>Get A Free Sample Package</p>
    <div class="back-rule"></div>
    <p class="back-url">www.BoldPromoPerksGroup.example</p>
  </section>
</main>
</body>
</html>
```